Tech business card design

We need an amazing business card design for our new business 'Pexla' a marketing tech startup based in Sydney, Australia. We provide an online marketplace for businesses to search and buy advertising media, connect with service providers and learn more about marketing. We wish to communicate 'cool tech', reliability and professionalism and design based around our logo.

Target Market(s)

Business Owners

Contact Information for Business Card

Name
Position
Email Address
Website
Phone Number

Font styles to use
Other font styles liked:
• Avenir & Avenir Next

Colors

Designer to choose colors to be used in the design.

```html
<!DOCTYPE html>
<html lang="en">
<head>
<meta charset="utf-8">
<title>Pexla Business Card</title>
<link rel="stylesheet" href="https://fonts.googleapis.com/css2?family=Source+Sans+3:wght@400;700;800&display=swap">
<style>
  :root {
    --backdrop: #e2dfdf;
    --card-white: #ffffff;
    --card-edge: #d6d4d4;
    --ink: #231f20;
    --navy-dark: #12123a;
    --navy: #24336b;
    --panel: #fbfbfe;
    --panel-edge: #1c1c28;
  }
  * { margin: 0; padding: 0; box-sizing: border-box; }
  html, body {
    width: 1079px; height: 1200px; overflow: hidden;
    background: var(--backdrop);
    font-family: "Source Sans 3", "Helvetica Neue", Arial, sans-serif;
    color: var(--ink);
  }
  .canvas { position: relative; width: 1079px; height: 1200px; }

  .card-front {
    position: absolute; left: 88px; top: 50px; width: 903px; height: 516px;
    background: var(--card-white); border: 1px solid var(--card-edge); border-radius: 33px;
  }
  .wordmark {
    position: absolute; font-weight: 800; color: var(--navy-dark);
    letter-spacing: -4px; line-height: 1;
  }
  .card-front .wordmark { right: 92px; top: 22px; font-size: 168px; }
  .holder-name {
    position: absolute; left: 70px; top: 258px; font-size: 31px; font-weight: 700; line-height: 1;
  }
  .holder-role {
    position: absolute; left: 70px; top: 297px; font-size: 27px; line-height: 1;
  }
  .divider {
    position: absolute; left: 65px; top: 342px; width: 773px; height: 2px; background: var(--navy-dark);
  }
  .contact-list { position: absolute; left: 70px; top: 373px; list-style: none; }
  .contact-list li {
    display: flex; align-items: center; height: 38px; font-size: 23px; line-height: 1;
  }
  .contact-list svg { width: 22px; height: 22px; margin-right: 10px; flex: none; }
  .contact-list .web { letter-spacing: 2.4px; }
  .address {
    position: absolute; right: 65px; top: 397px; text-align: right; font-size: 23px; line-height: 30px;
  }

  .card-back {
    position: absolute; left: 88px; top: 626px; width: 903px; height: 517px;
    background: var(--navy); border-radius: 33px;
  }
  .back-panel {
    position: absolute; left: 52px; top: 34px; width: 798px; height: 448px;
    background: var(--panel); border: 3px solid var(--panel-edge); border-radius: 26px;
  }
  .back-panel .wordmark {
    left: 0; right: 0; top: 128px; text-align: center; font-size: 168px;
  }
  .back-web {
    position: absolute; left: 0; right: 0; bottom: 4px; text-align: center;
    color: #ffffff; font-size: 29px; letter-spacing: 3.5px; line-height: 1;
  }
</style>
</head>
<body>
<main class="canvas">
  <section class="card-front">
    <div class="wordmark">pexla</div>
    <div class="holder-name">JOHN SMITH</div>
    <div class="holder-role">Position</div>
    <div class="divider"></div>
    <ul class="contact-list">
      <li>
        <svg viewBox="0 0 24 24" fill="none" stroke="#231f20" stroke-width="1.6">
          <circle cx="12" cy="12" r="10.5"/>
          <path d="M9 6.5 l2 3 -1.3 1.2 c.6 1.8 1.8 3 3.4 3.6 l1.2-1.3 3 2 -1.4 2 c-4.5-.4-8-4-8.4-8.5z" fill="#231f20" stroke="none"/>
        </svg>012-345-6789
      </li>
      <li>
        <svg viewBox="0 0 24 24">
          <rect x="1" y="5" width="22" height="14" fill="#231f20"/>
          <path d="M2 6 L12 13 L22 6 M2 18 L9 11 M22 18 L15 11" stroke="#ffffff" stroke-width="1.6" fill="none"/>
        </svg>info@pexla.com
      </li>
      <li class="web">
        <svg viewBox="0 0 24 24" fill="none" stroke="#231f20" stroke-width="1.4">
          <circle cx="12" cy="12" r="10.5"/>
          <ellipse cx="12" cy="12" rx="4.5" ry="10.5"/>
          <path d="M1.5 12 H22.5 M3.5 6.5 H20.5 M3.5 17.5 H20.5 M12 1.5 V22.5"/>
        </svg>www.pexla.com
      </li>
    </ul>
    <div class="address">Street name City Name,<br>Zipcode,012345</div>
  </section>

  <section class="card-back">
    <div class="back-panel">
      <div class="wordmark">pexla</div>
    </div>
    <div class="back-web">www.pexla.com</div>
  </section>
</main>
</body>
</html>
```